Executive Business Card for Healthcare Company [Need Today]

I need a business card design for a healthcare company. The only branding the company has thus far is a logo. The cards will be utilized by company executives. The design I envision will be vibrant and appealing but with a corporate feel. They shouldn't be too casual or playful. I would like to complete this project TODAY if possible.

Target Market(s)

Healthcare vendors, other executives in healthcare and pharmaceuticals

Industry/Entity Type

Pharmaceutical

Contact Information for Business Card

See attachment

Font styles to use
Serif
Sans Serif

Colors

Designer to choose colors to be used in the design.

```html
<!DOCTYPE html>
<html lang="en">
<head>
<meta charset="utf-8">
<title>Corvale Therapeutics – Business Card</title>
<link href="https://fonts.googleapis.com/css2?family=Arimo:wght@400;700&display=swap" rel="stylesheet">
<style>
  :root {
    --backdrop: #3a3a3a;
    --card-front: #ececec;
    --teal: #3bbfca;
    --mint: #5cc49a;
    --ink: #2a2a2a;
    --rule: #8a8a8a;
    --grad-mint: #6fd09c;
    --grad-teal: #3cbfcc;
    --white: #ffffff;
  }
  * { margin: 0; padding: 0; box-sizing: border-box; }
  html, body {
    width: 1200px; height: 900px; overflow: hidden;
    background: var(--backdrop);
    font-family: "Arimo", Arial, sans-serif;
  }
  .stage { position: relative; width: 1200px; height: 900px; }

  .card { position: absolute; top: 170px; width: 347px; height: 561px; overflow: hidden; }
  .card--front { left: 259px; background: var(--card-front); }
  .card--back { left: 631px; }

  /* front: brand */
  .brand { position: absolute; left: 31px; top: 111px; display: flex; align-items: center; gap: 22px; }
  .brand__circle { width: 88px; height: 88px; border: 3px solid var(--mint); border-radius: 50%; }
  .brand__name { color: var(--teal); font-weight: 400; line-height: 1; }
  .brand__name .line1 { display: block; font-size: 44px; letter-spacing: 1px; }
  .brand__name .line2 { display: block; font-size: 19px; text-align: right; margin-top: 4px; }

  /* front: contact */
  .contact { position: absolute; left: 0; right: 0; top: 310px; text-align: center; color: var(--ink); }
  .contact__name { font-size: 19px; font-weight: 700; letter-spacing: .3px; }
  .contact__name .first { color: var(--teal); }
  .contact__name .last { color: var(--mint); }
  .contact__title { font-size: 16px; margin-top: 3px; }
  .contact__icons { display: block; margin: 10px auto 6px; }
  .contact__lines p { font-size: 16px; line-height: 20px; }
  .contact__rule { width: 206px; height: 1px; background: var(--rule); margin: 9px auto 12px; }
  .company { font-size: 16px; font-weight: 700; color: var(--mint); letter-spacing: .2px; }
  .address p { font-size: 16px; line-height: 20px; }

  /* back */
  .back__field {
    position: absolute; inset: 0;
    background: linear-gradient(160deg, var(--grad-mint) 0%, var(--grad-teal) 35%, var(--grad-teal) 65%, var(--grad-mint) 100%);
  }
  .back__name {
    position: absolute; left: 24px; top: 412px;
    font-size: 72px; font-weight: 400; color: var(--white); letter-spacing: 2px;
  }
</style>
</head>
<body>
<main class="stage">
  <section class="card card--front">
    <div class="brand">
      <div class="brand__circle"></div>
      <div class="brand__name"><span class="line1">corvale</span><span class="line2">therapeutics</span></div>
    </div>

    <div class="contact">
      <h1 class="contact__name"><span class="first">DANIEL</span> <span class="last">MORROW</span></h1>
      <p class="contact__title">Senior Director of Marketing</p>

      <svg class="contact__icons" width="206" height="18" viewBox="0 0 206 18" aria-hidden="true">
        <line x1="0" y1="9" x2="72" y2="9" stroke="#8a8a8a" stroke-width="1"/>
        <line x1="134" y1="9" x2="206" y2="9" stroke="#8a8a8a" stroke-width="1"/>
        <g fill="none" stroke="#3bbfca" stroke-width="1.2">
          <circle cx="83" cy="9" r="8"/>
          <circle cx="103" cy="9" r="8"/>
          <circle cx="123" cy="9" r="8"/>
        </g>
        <g fill="#3bbfca">
          <path d="M79 7 q4 -3 8 0 v1.5 h-2 v-1 q-2 -1 -4 0 v1 h-2z M80 9 h6 l1 3 h-8z"/>
          <rect x="100.5" y="4" width="5" height="10" rx="1"/>
        </g>
        <rect x="101.5" y="5.5" width="3" height="6" fill="#ececec"/>
        <g fill="none" stroke="#3bbfca" stroke-width="1.2">
          <rect x="118.5" y="5.5" width="9" height="7"/>
          <polyline points="118.5,5.5 123,9.5 127.5,5.5"/>
        </g>
      </svg>

      <div class="contact__lines">
        <p>555-201-4837</p>
        <p>555-309-6214</p>
        <p>dmorrow@corvalerx.com</p>
      </div>
      <div class="contact__rule"></div>
      <p class="company">CORVALE THERAPEUTICS, LLC</p>
      <div class="address">
        <p>118 W Clayton Avenue</p>
        <p>Millbrook, GA 30092</p>
      </div>
    </div>
  </section>

  <section class="card card--back">
    <div class="back__field" role="img" aria-label="Repeating pattern of the company symbol over a mint-to-teal gradient"></div>
    <p class="back__name">corvale</p>
  </section>
</main>
</body>
</html>
```